Vernac Law Business cards and stationary design project

We are looking for a stationary design for business cards (double sided), 8x10, 5x7, and legal and standard envelopes.

We would like the design to match the logo that we have already.
Color palate preferred is Teal, White, grey and any others that will look good for a professional law firm.

We would like this statement: "RELATIONSHIPS. RESPECT. RESULT" to be on the back of the business cards and maybe on the stationary if it looks good.

Please see link to website for more information: www.vernac-law.example

Target Market(s)

Potential clients that need Attorney services.

Industry/Entity Type

Law Firm

Contact Information for Business Card

We would like the front and back to be two different colors. Current business cards are teal front, grey back and are a vertical design. We are open to options with colors.

Font styles to use
Serif

Colors
33a6d7
33b8a4
b9b9b9
5c5c5c

Requirements
Must have
• Logo supplied needs to go on the card and stationary.
• Match website color palate, www.vernac-law.example
• Be professional and not too wordy.
• Criminal Law, Civil Litigation, Personal Injury, Restraining Orders need to be on the card.
Nice to have
• RELATIONSHIPS. RESPECT. RESULTS. on the back of the card.
Should not have
• Not be too busy/wordy or too flashy.

```html
<!DOCTYPE html>
<html lang="en">
<head>
<meta charset="utf-8">
<title>Vernac Law – Stationery Set</title>
<link href="https://fonts.googleapis.com/css2?family=Cinzel:wght@400;500&display=swap" rel="stylesheet">
<style>
  :root {
    --teal: #128a9a;
    --teal-faint: #e4f0f2;
    --grey: #53544f;
    --backdrop: #d3d3d3;
    --paper: #ffffff;
    --gold: #d9c07a;
    --ink: #3a3a3a;
    --shadow: 3px 4px 6px rgba(0,0,0,0.28);
  }
  * { margin: 0; padding: 0; box-sizing: border-box; }
  html, body { width: 1200px; height: 900px; overflow: hidden; }
  body {
    background: var(--backdrop);
    font-family: "Cinzel", "Times New Roman", serif;
    position: relative;
  }
  .piece { position: absolute; background: var(--paper); box-shadow: var(--shadow); overflow: hidden; }

  .brand-name { color: var(--teal); font-weight: 400; letter-spacing: 0.04em; white-space: nowrap; }
  .brand-faint {
    position: absolute; color: var(--teal-faint); font-weight: 400;
    white-space: nowrap; line-height: 1; pointer-events: none;
  }
  .contact { font-size: 7px; line-height: 10px; color: var(--ink); letter-spacing: 0.05em; }

  /* Envelope back */
  .envelope-back { left: 64px; top: 147px; width: 519px; height: 258px; }
  .envelope-back svg { position: absolute; left: 0; top: 0; }

  /* Envelope front */
  .envelope-front { left: 123px; top: 259px; width: 519px; height: 259px; }
  .envelope-front .brand-faint { left: 150px; top: 70px; font-size: 120px; transform: rotate(-8deg); }
  .envelope-front .brand-name { position: absolute; left: 22px; top: 44px; font-size: 13px; }
  .envelope-front .contact { position: absolute; left: 21px; top: 78px; }

  /* Business card front */
  .card-front { left: 61px; top: 539px; width: 282px; height: 169px; background: var(--teal); }
  .card-front .brand-name {
    position: absolute; left: 0; right: 0; top: 76px; text-align: center;
    color: var(--paper); font-size: 19px;
  }
  .card-front .rule { position: absolute; left: 0; right: 0; top: 121px; height: 3px; background: var(--grey); }
  .card-front .band {
    position: absolute; left: 0; right: 0; top: 127px; bottom: 0; background: var(--grey);
    display: flex; align-items: center; justify-content: center; gap: 8px;
  }
  .card-front .contact { color: var(--paper); font-size: 6.5px; line-height: 9px; }
  .card-front .contact.address { text-align: right; padding-right: 8px; border-right: 1px solid rgba(255,255,255,0.6); }

  /* Business card back */
  .card-back { left: 359px; top: 539px; width: 282px; height: 169px; }
  .card-back .heading {
    position: absolute; left: 0; right: 0; top: 34px; text-align: center;
    font-size: 7px; letter-spacing: 0.35em; color: var(--ink);
  }
  .card-back .practice {
    position: absolute; left: 0; right: 0; top: 55px; height: 54px; background: var(--grey);
    color: var(--paper); font-size: 8px; line-height: 11px; text-align: center;
    display: flex; flex-direction: column; justify-content: center;
  }
  .card-back .motto {
    position: absolute; left: 0; right: 0; top: 124px; text-align: center;
    font-size: 8.5px; letter-spacing: 0.3em; color: var(--ink);
  }

  /* Letterhead */
  .letterhead { left: 665px; top: 113px; width: 475px; height: 669px; }
  .letterhead .brand-faint { left: 10px; top: 300px; font-size: 190px; transform: rotate(-12deg); }
  .letterhead .brand-name { position: absolute; left: 22px; top: 70px; font-size: 16px; }
  .letterhead .divider { position: absolute; left: 143px; top: 29px; width: 1px; height: 60px; background: var(--gold); }
  .letterhead .contact { position: absolute; left: 147px; top: 30px; color: var(--teal); }
  .letterhead .contact p + p { margin-top: 8px; }
  .letterhead .foot-band { position: absolute; left: 0; right: 0; bottom: 0; height: 9px; background: var(--teal); }
</style>
</head>
<body>

  <div class="piece envelope-back">
    <svg width="519" height="258" viewBox="0 0 519 258" aria-hidden="true">
      <polygon points="0,0 519,0 486,62 33,62" fill="var(--teal)"/>
    </svg>
  </div>

  <div class="piece envelope-front">
    <div class="brand-faint">Vernac Law</div>
    <div class="brand-name">Vernac Law</div>
    <div class="contact">
      <p>Southern California,</p>
      <p>1480 Marlow Ave. #200</p>
      <p>Bayview Beach, CA 90299</p>
      <p>(555) 214-6038 &nbsp;|&nbsp; info@vernac-law.example</p>
    </div>
  </div>

  <div class="piece card-front">
    <div class="brand-name">Vernac Law</div>
    <div class="rule"></div>
    <div class="band">
      <div class="contact address">
        <p>Southern California,</p>
        <p>1480 Marlow Ave. #200</p>
        <p>Bayview Beach, CA 90299</p>
      </div>
      <div class="contact">
        <p>(555) 214-6038</p>
        <p>info@vernac-law.example</p>
      </div>
    </div>
  </div>

  <div class="piece card-back">
    <div class="heading">Practice Areas:</div>
    <div class="practice">
      <p>Criminal Law</p>
      <p>Civil Litigation / Personal Injury</p>
      <p>Restraining Orders</p>
    </div>
    <div class="motto">Relationships. Respect. Result.</div>
  </div>

  <div class="piece letterhead">
    <div class="brand-faint">Vernac Law</div>
    <div class="brand-name">Vernac Law</div>
    <div class="divider"></div>
    <div class="contact">
      <p>Southern California,<br>1480 Marlow Ave. #200<br>Bayview Beach, CA 90299</p>
      <p>(555) 214-6038<br>info@vernac-law.example</p>
    </div>
    <div class="foot-band"></div>
  </div>

</body>
</html>
```